Vantoq Business Card Project showing the logo and a marbo image on the rear

Design a whacky but professional business card, the logo is for the front and the Marbo image is for the rear. Happy to consider other open source Marbo Images if the designer wants to select one from the web. Vantoq is a competitor to OMB.com.au and Pellory.com.au and is based around every property in Australia

Target Market(s)

Business

Contact Information for Business Card

Name, Title, Email, Web, Phone Number

Font styles to use
Other font styles liked:
• avenir

Requirements
Must have
• Image on Back logo on front
Nice to have
• Happy to consider other images on rear, preftably Colin Marbo. Image supplied I own, we can use open source other Marbo Images

```html
<!DOCTYPE html>
<html lang="en">
<head>
<meta charset="utf-8">
<title>Vantoq Business Card</title>
<link href="https://fonts.googleapis.com/css2?family=Kumbh+Sans:wght@600;700&family=Roboto:wght@400&display=swap" rel="stylesheet">
<style>
  :root {
    --stage: #2b2b2b;
    --card: #f1f1f1;
    --ink: #161616;
    --orange: #ee8a12;
    --sky-day: #f08a0c;
    --sky-night: #3a3b3d;
    --white: #ffffff;
  }
  html, body { margin: 0; padding: 0; overflow: hidden; }
  body { width: 1200px; height: 1138px; background: var(--stage); position: relative; }

  .card { position: absolute; border-radius: 16px; overflow: hidden; }

  .card-rear { left: 274px; top: 186px; width: 622px; height: 374px; }
  .rear-art {
    width: 100%; height: 100%;
    background:
      linear-gradient(180deg, transparent 0%, transparent 58%, rgba(230,70,140,.55) 62%, rgba(150,200,60,.7) 80%, #5fb6c9 92%, #7cc243 100%),
      linear-gradient(90deg, var(--sky-day) 0%, var(--sky-day) 49.5%, var(--sky-night) 50.5%, var(--sky-night) 100%);
  }

  .card-front { left: 276px; top: 608px; width: 618px; height: 374px; background: linear-gradient(180deg, #f7f7f7, #e9e9e9); }

  .brand { position: absolute; left: 34px; top: 42px; display: flex; align-items: center; gap: 34px; }
  .brand-mark { width: 72px; height: 72px; background: var(--orange); }
  .brand-name { font-family: "Kumbh Sans", sans-serif; font-weight: 700; font-size: 70px; color: var(--ink); letter-spacing: 0.5px; line-height: 1; }

  .person { position: absolute; left: 33px; top: 198px; font-family: Roboto, sans-serif; }
  .person-name { font-family: "Kumbh Sans", sans-serif; font-weight: 600; font-size: 25px; color: var(--orange); margin: 0; line-height: 1.1; }
  .person-title { font-size: 16px; color: var(--ink); margin: 4px 0 0; }

  .address { position: absolute; left: 33px; top: 290px; font-family: Roboto, sans-serif; font-size: 16px; line-height: 21px; color: var(--ink); margin: 0; font-style: normal; }

  .contacts { position: absolute; left: 344px; top: 202px; list-style: none; margin: 0; padding: 0; font-family: Roboto, sans-serif; font-size: 16px; color: var(--ink); }
  .contacts li { display: flex; align-items: center; height: 23.5px; }
  .contacts svg { width: 13px; height: 13px; margin-right: 18px; fill: var(--orange); }
  .contacts .accent { color: var(--orange); }

  .base-strip { position: absolute; left: 0; bottom: 0; width: 300px; height: 16px; background: var(--ink); }
  .tagline-band {
    position: absolute; right: 0; bottom: 0; width: 354px; height: 46px;
    background: var(--orange);
    clip-path: polygon(22px 0, 100% 0, 100% 100%, 0 100%);
    border-top-left-radius: 10px;
    font-family: Roboto, sans-serif; font-size: 16px; color: var(--white);
    display: flex; align-items: center; padding-left: 76px; box-sizing: border-box;
  }
</style>
</head>
<body>

<section class="card card-rear">
  <div class="rear-art" role="img" aria-label="Colourful cartoon city skyline artwork: smiling buildings under a half day, half night sky with sun, clouds, stars, music notes and a plane, above a train"></div>
</section>

<section class="card card-front">
  <div class="brand">
    <span class="brand-mark"></span>
    <span class="brand-name">Vantoq</span>
  </div>

  <div class="person">
    <h1 class="person-name">Owen Prescot</h1>
    <p class="person-title">Founder &amp; CEO</p>
  </div>

  <address class="address">Level 4, 18 Harbour Lane,<br>Sydney 2000, Australia</address>

  <ul class="contacts">
    <li>
      <svg viewBox="0 0 16 16"><path d="M8 0a8 8 0 1 0 0 16A8 8 0 0 0 8 0zm0 1.6a6.4 6.4 0 1 1 0 12.8A6.4 6.4 0 0 1 8 1.6zM5.6 4l1.3-.2.8 2-1 .8c.5 1.1 1.3 1.9 2.4 2.4l.8-1 2 .8-.2 1.3c-.2.6-.8.9-1.4.8C7.7 10.3 5.7 8.3 5.3 5.4c-.1-.6.2-1.2.3-1.4z"/></svg>
      (00) 4417 8620
    </li>
    <li>
      <svg viewBox="0 0 16 16"><path d="M0 3h16v1.2L8 9 0 4.2zM0 5.8l8 4.8 8-4.8V13H0z"/></svg>
      prescot@vantoq.com
    </li>
    <li>
      <svg viewBox="0 0 16 16"><path d="M8 0a8 8 0 1 0 0 16A8 8 0 0 0 8 0zM2 7.3h2.7c.1-1.9.5-3.5 1.1-4.7A6.4 6.4 0 0 0 2 7.3zm4.3 0h3.4C9.6 5 9 3.1 8 1.8 7 3.1 6.4 5 6.3 7.3zm5 0H14a6.4 6.4 0 0 0-3.8-4.7c.6 1.2 1 2.8 1.1 4.7zM2 8.7a6.4 6.4 0 0 0 3.8 4.7c-.6-1.2-1-2.8-1.1-4.7zm4.3 0c.1 2.3.7 4.2 1.7 5.5 1-1.3 1.6-3.2 1.7-5.5zm5 0c-.1 1.9-.5 3.5-1.1 4.7A6.4 6.4 0 0 0 14 8.7z"/></svg>
      <span>www.<span class="accent">vantoq</span>.com</span>
    </li>
  </ul>

  <div class="base-strip"></div>
  <div class="tagline-band">Buying, Selling and Research</div>
</section>

</body>
</html>
```